Building company buisness cards

We are looking for a sharp modern new look for our business cards.
We are a New Zealand based company that specialises in house and land packages.
We have attached a photo of the current logo and would like to see if it can be improved somehow if needed.
We are open to any colours but we have chosen green at this stage.
Feel free to change the font and make the logo smarter looking.
Play with the colours and see what looks best.

We want a card that looks so good know one will want to throw it away!

Target Market(s)

Home buyers

Industry/Entity Type

Building

Contact Information for Business Card

Derek Tolvane
0217394062
dtolvane@quillmarkhomesteads.co.nz
quillmarkhomesteads.co.nz

Font styles to use
Serif
Sans Serif

Colors

Designer to choose colors to be used in the design.

Requirements
Must have
• Logo and company name on one side, details on the other side
Nice to have
• Color codes for the original green are HEX #4a8028, RGB(74,128,40), CMYK(42,0,69,50)
• Round corners, Raised and/or spot UV

```html
<!DOCTYPE html>
<html lang="en">
<head>
<meta charset="utf-8">
<title>Quillmark Homesteads – Business Cards</title>
<link rel="stylesheet" href="https://fonts.googleapis.com/css2?family=Open+Sans:wght@400;600&display=swap">
<style>
  :root {
    --brand-green: #4a8028;
    --brand-green-bright: #4f9a2a;
    --brand-green-soft: #e4efdc;
    --card-white: #ffffff;
    --text-grey: #4a4a4a;
    --backdrop: #2b2c2e;
  }
  * { box-sizing: border-box; margin: 0; padding: 0; }
  html, body { width: 1200px; height: 885px; overflow: hidden; }
  body { background: var(--backdrop); position: relative; font-family: "Open Sans", sans-serif; }

  .card {
    position: absolute;
    width: 680px;
    height: 388px;
    background: var(--card-white);
    border-radius: 4px;
    overflow: hidden;
  }
  .card--front { left: 140px; top: 40px; }
  .card--back  { left: 380px; top: 457px; }

  .company-name {
    display: flex;
    align-items: center;
    font-family: "Open Sans", sans-serif;
    font-weight: 600;
    color: var(--brand-green);
    white-space: nowrap;
  }
  .company-name__square {
    flex: none;
    background: var(--brand-green);
  }

  .card--front .company-name {
    position: absolute;
    left: 0; right: 0; top: 170px;
    justify-content: center;
    font-size: 34px;
  }
  .card--front .company-name__square { width: 22px; height: 22px; margin-right: 14px; }

  .card--back .company-name {
    position: absolute;
    left: 40px; top: 70px;
    font-size: 22px;
  }
  .card--back .company-name__square { width: 14px; height: 14px; margin-right: 10px; }

  .brand-mark-area {
    position: absolute;
    right: 30px; top: 24px;
    width: 300px; height: 260px;
    border-radius: 6px;
    background: linear-gradient(160deg, var(--brand-green-soft), #cfe3c1);
  }

  .holder {
    position: absolute;
    left: 0; top: 250px;
    display: flex; align-items: center;
  }
  .holder__bar { width: 14px; height: 22px; background: var(--brand-green-bright); margin-right: 22px; }
  .holder__name {
    font-weight: 600; font-size: 22px; letter-spacing: 0.5px;
    color: var(--brand-green-bright); text-transform: uppercase;
  }

  .contact-list { position: absolute; left: 36px; top: 290px; list-style: none; }
  .contact-list li {
    display: flex; align-items: center;
    font-size: 17px; color: var(--text-grey);
    line-height: 24px;
  }
  .contact-list svg { width: 14px; height: 14px; margin-right: 10px; fill: var(--brand-green); }
</style>
</head>
<body>

  <section class="card card--front" aria-label="Card front">
    <div class="company-name">
      <span class="company-name__square"></span>
      <span>Quillmark Homesteads</span>
    </div>
  </section>

  <section class="card card--back" aria-label="Card back">
    <div class="company-name">
      <span class="company-name__square"></span>
      <span>Quillmark Homesteads</span>
    </div>

    <div class="brand-mark-area" role="img" aria-label="Large brand symbol of a roof sheltering a family"></div>

    <div class="holder">
      <span class="holder__bar"></span>
      <span class="holder__name">Derek Tolvane</span>
    </div>

    <ul class="contact-list">
      <li>
        <svg viewBox="0 0 16 16" aria-hidden="true"><path d="M3 2h3l1 4-2 1a9 9 0 0 0 4 4l1-2 4 1v3a1 1 0 0 1-1 1A12 12 0 0 1 2 3a1 1 0 0 1 1-1z"/></svg>
        0217394062
      </li>
      <li>
        <svg viewBox="0 0 16 16" aria-hidden="true"><path d="M1 3h14v10H1z M1 3l7 6 7-6" stroke="#fff" stroke-width="1.2"/></svg>
        dtolvane@quillmarkhomesteads.co.nz
      </li>
      <li>
        <svg viewBox="0 0 16 16" aria-hidden="true"><circle cx="8" cy="8" r="7"/><path d="M5 8h6M8 5l3 3-3 3" stroke="#fff" stroke-width="1.4" fill="none"/></svg>
        quillmarkhomesteads.co.nz
      </li>
    </ul>
  </section>

</body>
</html>
```